Young, dynamic furniture company needs a new business card design

We require a new business card design for our modern furniture company which supplies furniture and appliances to the property and development market.
Oakridge Interiors has become one of the leading furniture & appliance suppliers to the property market withing London. With over 10 years experience, we have increased our business to supply not only private landlords and managing agents, but also property developers, housing associations and local councils.
We offer not only a complete range of furniture which includes beds, wardrobes, dining sets and sofas, but also a high quality, full delivery and assembly service to help you with all our furnishing needs.

Target Market(s)

Private landlords, estate agents, letting agents, property management companies

Industry/Entity Type

Business

Contact Information for Business Card

Name,
Title,
Address,
Mobile,
Telephone,
Fax, Website, email address

Font styles to use
Sans Serif

Colors
3176b5
0555a3
85abd2
cfdeed

Requirements
Must have
• All the above information for each of our staff, along with our logo

```html
<!DOCTYPE html>
<html lang="en">
<head>
<meta charset="utf-8">
<title>Oakridge Interiors – Business Card</title>
<link href="https://fonts.googleapis.com/css2?family=Lato:wght@300;400;700&display=swap" rel="stylesheet">
<style>
  :root {
    --navy: #2f3b70;
    --blue: #2a6db5;
    --ink: #141414;
    --paper: #ffffff;
    --stage: #e9ecf1;
    --muted: #c9d3ea;
  }
  * { margin: 0; padding: 0; box-sizing: border-box; }
  html, body { width: 1200px; height: 900px; overflow: hidden; }
  body {
    background: var(--stage);
    font-family: "Lato", Arial, sans-serif;
    color: var(--ink);
    position: relative;
  }
  .card {
    position: absolute;
    width: 560px;
    height: 320px;
    left: 320px;
    border-radius: 4px;
    overflow: hidden;
    box-shadow: 0 10px 28px rgba(20, 30, 60, 0.18);
  }
  /* Back side */
  .card-back {
    top: 90px;
    background: var(--navy);
    color: var(--paper);
    display: flex;
    flex-direction: column;
    align-items: center;
    justify-content: center;
    text-align: center;
  }
  .brand {
    display: flex;
    align-items: center;
    gap: 12px;
  }
  .brand-square {
    width: 22px;
    height: 22px;
    background: var(--blue);
  }
  .card-back .brand-square { background: var(--paper); }
  .brand-name {
    font-weight: 300;
    font-size: 28px;
    letter-spacing: 0.5px;
    text-transform: uppercase;
  }
  .tagline {
    font-weight: 300;
    font-size: 12px;
    letter-spacing: 0.5px;
    text-transform: uppercase;
    margin-top: 6px;
  }
  .card-back .tagline { color: var(--muted); }
  .card-back .site {
    margin-top: 22px;
    font-size: 15px;
    letter-spacing: 2px;
  }
  /* Front side */
  .card-front {
    top: 450px;
    background: var(--paper);
  }
  .front-brand {
    position: absolute;
    left: 34px;
    top: 30px;
  }
  .front-brand .brand-name { font-size: 24px; color: var(--ink); }
  .front-brand .tagline { font-size: 10px; color: var(--ink); margin-left: 34px; margin-top: 2px; }
  .rule {
    position: absolute;
    left: 34px;
    right: 34px;
    top: 118px;
    height: 1px;
    background: var(--blue);
  }
  .contacts {
    position: absolute;
    left: 34px;
    top: 138px;
    list-style: none;
    font-size: 14px;
    line-height: 22px;
  }
  .contacts li { display: flex; align-items: center; gap: 10px; }
  .contacts svg { width: 12px; height: 12px; fill: var(--blue); }
  .person {
    position: absolute;
    right: 34px;
    top: 138px;
    text-align: right;
  }
  .person-name { font-size: 24px; font-weight: 400; }
  .person-title {
    font-size: 16px;
    font-weight: 300;
    color: var(--blue);
    border-top: 1px solid var(--blue);
    display: inline-block;
    padding-top: 2px;
    margin-top: 2px;
  }
  .address { font-size: 14px; line-height: 19px; margin-top: 10px; }
  .footer-band { position: absolute; left: 0; bottom: 0; width: 560px; height: 44px; }
  .footer-site {
    position: absolute;
    right: 34px;
    bottom: 10px;
    color: var(--paper);
    font-size: 15px;
    letter-spacing: 1.5px;
  }
</style>
</head>
<body>

<section class="card card-back">
  <div class="brand">
    <span class="brand-square"></span>
    <span class="brand-name">Oakridge Interiors</span>
  </div>
  <p class="tagline">Trade Furniture Solutions</p>
  <p class="site">www.trade.oakridgeint.co.uk</p>
</section>

<section class="card card-front">
  <div class="front-brand">
    <div class="brand">
      <span class="brand-square"></span>
      <span class="brand-name">Oakridge Interiors</span>
    </div>
    <p class="tagline">Trade Furniture Solutions</p>
  </div>

  <div class="rule"></div>

  <ul class="contacts">
    <li><svg viewBox="0 0 12 12"><path d="M2.5 0.5 L4.5 0.5 L5 3.5 L3.6 4.5 C4.3 6 5.6 7.4 7.3 8.2 L8.3 6.9 L11.5 7.4 L11.5 9.6 C11.5 10.8 10.4 11.6 9.2 11.4 C5 10.6 1.4 7 0.6 2.8 C0.4 1.6 1.2 0.5 2.5 0.5 Z"/></svg>020 7946 0321</li>
    <li><svg viewBox="0 0 12 12"><path d="M3 0 H9 A1 1 0 0 1 10 1 V11 A1 1 0 0 1 9 12 H3 A1 1 0 0 1 2 11 V1 A1 1 0 0 1 3 0 Z M3.4 1.4 V9.4 H8.6 V1.4 Z"/></svg>020 7946 0000</li>
    <li><svg viewBox="0 0 12 12"><path d="M0 2 H12 V10 H0 Z M0.8 2.6 L6 6.6 L11.2 2.6" stroke="#fff" stroke-width="0.8"/></svg>info@trade.oakridgeint.co.uk</li>
  </ul>

  <div class="person">
    <p class="person-name">Daniel Hartley</p>
    <p class="person-title">Manager</p>
    <p class="address">27B Harlow Business Park<br>Elmstead, London</p>
  </div>

  <svg class="footer-band" viewBox="0 0 560 44" preserveAspectRatio="none">
    <polygon points="0,14 250,30 250,44 0,44" fill="var(--blue)"/>
    <polygon points="275,18 560,18 560,44 250,44" fill="var(--navy)"/>
  </svg>
  <p class="footer-site">www.trade.oakridgeint.co.uk</p>
</section>

</body>
</html>
```